Insert sheet for our Dog Food Package

We need an information sheet to go inn our pet food package, with branding, and information on ingredients, nutrition and feeding guidance. We will also need two additional items which will be a variation on the label design:
1) Label for package (detailed label about us and our food)
2) Label for outer shipping box (simple label for branding)
We will start with the information, insert page. The winning designer will then deliver the package and box labels as simplified versions of the same graphical theme.
I have attached samples of an earlier drafts of the insert piece. Please disregard the style, form and colors of the examples given. THEY ARE ONLY THERE TO SHOW WHAT INFORMATION SHOULD BE INCLUDED. All colors and style should be from our logo (attached). All graphics, font styles, and placement of elements need to be YOUR creative design - not a copy of the sample we gave. PLEASE READ THIS AND PLEASE DO NOT SUBMIT ANY VARIATION OF THE EXAMPLES!!!!!!!

Target Market(s)

Pet Owners

Industry/Entity Type

Pet Food

Colors
EB3D1F
EC4F4E
F09395
F8D3D4
FCEDEE

Requirements
Must have
• All new design. New colors (based in the palette of our logo), new graphics, new fonts, new placement of elements.
Should not have
• Please disregard the style, form and colors of the examples given. THEY ARE ONLY THERE TO SHOW WHAT INFORMATION SHOULD BE INCLUDED.

```html
<!DOCTYPE html>
<html lang="en">
<head>
<meta charset="utf-8">
<title>Varo – Food Insert Sheet</title>
<link rel="stylesheet" href="https://fonts.googleapis.com/css2?family=Ubuntu:wght@300;400;500;700&display=swap">
<style>
:root{
  --stage:#2b2b2b;
  --maroon:#471510;
  --maroon-deep:#3a0f0b;
  --red:#a81f22;
  --red-bright:#b82327;
  --white:#ffffff;
  --paper:#f4f4f4;
  --ink:#2a2a2a;
  --rule:#2e2e2e;
  --row:#ececec;
}
*{box-sizing:border-box;margin:0;padding:0}
html,body{width:1200px;height:875px;overflow:hidden;background:var(--stage)}
body{font-family:'Ubuntu',sans-serif;color:var(--ink)}
.sheet{position:absolute;left:287px;top:10px;width:626px;height:855px;background:var(--paper);overflow:hidden}
.sheet-bg{position:absolute;inset:0}
.frame{position:absolute;left:18px;top:19px;right:18px;bottom:20px;border:5px solid var(--red);pointer-events:none;z-index:5}

.brand-mark{position:absolute;left:119px;top:61px;width:157px;height:157px;border-radius:50%;background:var(--red);border:8px solid var(--white)}
.brand-name{position:absolute;left:284px;top:92px;font-weight:500;font-size:64px;letter-spacing:8px;color:var(--red-bright);line-height:1}

.story{position:absolute;left:0;right:0;top:290px;text-align:center}
.story-title{display:flex;align-items:center;justify-content:center;gap:12px;font-weight:700;font-size:40px;color:var(--ink);line-height:36px}
.story-title::before,.story-title::after{content:"";width:122px;height:2px;background:var(--maroon)}
.story-lead{margin-top:9px;font-size:19px;line-height:25px;font-weight:500;white-space:nowrap}
.story-quote{margin-top:7px;font-size:11.6px;line-height:15.5px;white-space:nowrap}

.love-title{position:absolute;left:0;right:0;top:488px;text-align:center;color:var(--white);font-weight:700;font-size:29px;line-height:36px;letter-spacing:.3px}

.panel{position:absolute;top:533px;height:283px;border:2px solid var(--rule);background:var(--white)}
.panel-nutrition{left:41px;width:266px}
.panel-feeding{left:320px;width:266px}
.panel-head{background:var(--red);color:var(--white);font-weight:500;font-size:15.5px;height:41px;display:flex;align-items:center;justify-content:center;white-space:nowrap}
.panel-sub{background:var(--maroon-deep);color:var(--white);font-size:17px;height:36px;display:flex;align-items:center;justify-content:center;letter-spacing:.2px;white-space:nowrap}

.nutri-grid{display:grid;grid-template-columns:1fr 1fr}
.nutri-cell{display:flex;justify-content:space-between;padding:0 10px 0 16px;height:22px;align-items:center;font-size:13px;font-weight:500;border-bottom:2px solid var(--rule);white-space:nowrap}
.nutri-cell:nth-child(odd){border-right:2px solid var(--rule)}
.ingredients{padding:9px 8px 0;text-align:center;font-size:12.3px;line-height:16.3px}

.feed-table{width:100%;border-collapse:collapse;font-size:13px;white-space:nowrap}
.feed-table th{font-weight:500;font-size:15.5px;text-align:left;height:33px;border-bottom:3px solid var(--rule)}
.feed-table td{height:19px;background:var(--row)}
.feed-table th:first-child,.feed-table td:first-child{padding-left:14px;width:64%}
.feed-table tr.group-end td{border-bottom:3px solid var(--rule);padding-bottom:5px}
.feed-table tr.group-start td{padding-top:6px}
.feed-table tr.single td{height:28px;padding-top:0;padding-bottom:0}
</style>
</head>
<body>
<main class="sheet">
  <svg class="sheet-bg" width="626" height="855" viewBox="0 0 626 855" aria-hidden="true">
    <defs>
      <linearGradient id="hero" x1="0" y1="0" x2="0" y2="1">
        <stop offset="0" stop-color="#4f1912"/>
        <stop offset="1" stop-color="#3c0f0b"/>
      </linearGradient>
    </defs>
    <rect width="626" height="310" fill="url(#hero)"/>
    <path d="M0,283 C140,250 300,236 626,240 L626,320 L0,320 Z" fill="#a81f22"/>
    <path d="M0,302 C150,280 330,236 450,237 C530,238 585,246 626,252 L626,480 L0,480 Z" fill="#f4f4f4"/>
    <rect y="480" width="626" height="72" fill="#471510"/>
  </svg>

  <div class="frame"></div>

  <header class="brand">
    <div class="brand-mark" role="img" aria-label="Brand emblem area"></div>
    <div class="brand-name">VARO</div>
  </header>

  <section class="story">
    <h2 class="story-title">OUR STORY</h2>
    <p class="story-lead">We Revolutionzed the industry. Not Formulated to<br>meed a minimum standard, but to develop the maximum<br>health of the whole dog.</p>
    <p class="story-quote">“we didn’t just set about to create a food that will ‘pass a minimum standard”. We set out to<br>revolutionize the industry by creating a food that is designed with Superfoods, Wholesie Grains,<br>and Powerful Oil to help your dog achieve their maximum health, happiness andlongevity.</p>
  </section>

  <h2 class="love-title">PREPARED WITH LOVE FOR BISCUIT</h2>

  <section class="panel panel-nutrition">
    <div class="panel-head">We Prepared the best for biscuit</div>
    <div class="panel-sub">NUTRITIONAL INFORMATION</div>
    <div class="nutri-grid">
      <div class="nutri-cell"><span>Protein:</span><span>15%</span></div>
      <div class="nutri-cell"><span>Total Fat:</span><span>9.5%</span></div>
      <div class="nutri-cell"><span>Crude Fiber: 2.0%</span></div>
      <div class="nutri-cell"><span>Moisture:</span><span>72%</span></div>
    </div>
    <p class="ingredients">Potassium Citrate, DiCalcium Phosphate,<br>Calcium Carbonate, Garbanzo Beans,<br>Choline Bitartrate, Taurine, Salt, Zinc<br>Proteinate, Magnesium Oxide, Iron<br>Proteinate, Vitamin B-12, Selenium,<br>Niacin, Riboflavin, Calcium Panthothenate,<br>Thiamine, Vitamin A, Vitamin D,<br>Calcium Lodate, Vitamin B6, Folic Acid</p>
  </section>

  <section class="panel panel-feeding">
    <div class="panel-head">How much should i feed biscuit?</div>
    <div class="panel-sub">RECOMMENDED FEEDING PLAN</div>
    <table class="feed-table">
      <thead><tr><th>Approximate weight</th><th>Full meal</th></tr></thead>
      <tbody>
        <tr class="single group-end"><td>&lt;20 lbs</td><td>110 g</td></tr>
        <tr class="group-start"><td>20-29 lbs</td><td>200 g</td></tr>
        <tr><td>30-39 lbs</td><td>250 g</td></tr>
        <tr class="group-end"><td>40-54 lbs</td><td>300 g</td></tr>
        <tr class="group-start"><td>50-69 lbs</td><td>350 g</td></tr>
        <tr class="group-end"><td>70-85 lbs</td><td>400 g</td></tr>
        <tr class="single"><td>85+ lbs</td><td>500 g</td></tr>
      </tbody>
    </table>
  </section>
</main>
</body>
</html>
```